VELMA, an e-commerce website with a twist, providing consumer-to-consumer and business-to-consumer sa

I have only uploaded 10 wire-frame pages of the website. These pages have been chosen for the different lay-outs and should give an idea of what will be needed. There are many more that I won’t upload yet, I aim to choose a winner first then there will be a high possibility that the winner will get the chance to do the design work for these later.
The design I have in mind is to keep it clean and easy with no/minimal fancy fonts and hieroglyphics. The logo is white with an orange highlight on a solid background of black, please note that the logo is white on a black background and is not a black box with white lettering, trust that makes sense. I like the idea of the top part of the website being black all the way across. I don’t see the need for more than 3 colours in the actual base website (the pictures and adverts added by users will add other colours). Although orange is the highlight colour in the logo I am open to suggestions on this, so long as the highlight colour features throughout the site.

Website width is 1220px, all pages in the PDF are 1220px

Logo font is Rezlong

The company is going to be like tradu, but much more focused on raising money for charity and humanitarian relief.

Target Market(s)

the modern era of smartphones and the sharing community

Industry/Entity Type

Business

Number of Pages Required

5+ page

Font styles to use
Sans Serif
Other font styles liked:
• rezlong

Colors
faa54b
f78f20
ffffff
000000
fbfbfb
f5f5f5

Requirements
Nice to have
• Although orange is the highlight colour in the logo I am open to suggestions on this, so long as the highlight colour features throughout the site.

```html
<!DOCTYPE html>
<html lang="en">
<head>
<meta charset="utf-8">
<title>VELMA – Home</title>
<link href="https://fonts.googleapis.com/css2?family=Comfortaa:wght@400;700&family=Open+Sans:ital,wght@0,400;0,600;1,400&display=swap" rel="stylesheet">
<style>
:root{
  --orange:#f78f20;
  --orange-light:#faa54b;
  --black:#000000;
  --white:#ffffff;
  --off-white:#fbfbfb;
  --grey-bg:#f2f2f2;
  --grey-line:#c9c9c9;
  --text:#333333;
  --muted:#666666;
}
*{box-sizing:border-box;margin:0;padding:0}
html,body{width:705px;height:1200px;overflow:hidden;background:var(--white)}
body{position:relative;font-family:"Open Sans",Arial,sans-serif;color:var(--text)}
.abs{position:absolute}

/* utility bar */
.utility-bar{left:0;top:0;width:705px;height:33px;background:var(--grey-bg)}
.utility-bar a{position:absolute;top:11px;font-family:"Comfortaa",sans-serif;font-size:8px;color:var(--black);text-decoration:none}
.site-search{position:absolute;left:570px;top:0;width:135px;height:33px;border-left:1px solid var(--grey-line);background:var(--white)}
.site-search span{position:absolute;left:10px;top:11px;font-size:8px;color:var(--muted)}
.site-search svg{position:absolute;right:10px;top:11px}

/* header */
.masthead{left:0;top:33px;width:705px;height:51px;background:var(--black)}
.brand{position:absolute;left:24px;top:10px;font-family:"Comfortaa",sans-serif;font-weight:700;font-size:28px;color:var(--white);letter-spacing:1px}
.main-nav a{position:absolute;top:21px;font-family:"Comfortaa",sans-serif;font-size:9px;color:var(--white);text-decoration:none}

/* hero */
.hero{left:0;top:84px;width:705px;height:310px;background:radial-gradient(ellipse at 50% 40%,var(--orange-light),var(--orange) 75%)}
.media-tile{position:absolute;border:3px solid var(--white);display:flex;align-items:center;justify-content:center}
.play-ring{width:30px;height:30px}
.search-panel{position:absolute;left:249px;top:26px;width:208px;height:254px;background:var(--white)}
.search-panel h2{height:32px;background:var(--black);color:var(--white);font-family:"Comfortaa",sans-serif;font-weight:700;font-size:17px;padding:6px 12px}
.field-label{position:absolute;left:12px;font-size:8.5px;font-weight:600;color:var(--text)}
.field{position:absolute;left:12px;width:170px;height:23px;border:1px solid var(--grey-line);font-size:8px;color:var(--muted);padding:6px 9px}
.help-dot{position:absolute;left:190px;width:9px;height:9px;border-radius:50%;background:var(--orange);color:var(--white);font-size:7px;font-weight:600;text-align:center;line-height:9px}
.search-button{position:absolute;left:12px;top:216px;width:184px;height:27px;background:var(--orange);color:var(--white);font-family:"Comfortaa",sans-serif;font-weight:700;font-size:13px;text-align:center;line-height:27px}
.item-card{position:absolute;left:474px;width:208px;height:78px;background:var(--white)}
.item-thumb{position:absolute;left:9px;top:10px;width:72px;height:58px}
.item-card h3{position:absolute;left:90px;top:8px;font-family:"Comfortaa",sans-serif;font-weight:700;font-size:9px;color:var(--black)}
.item-card p{position:absolute;left:90px;top:22px;width:106px;font-size:8.5px;line-height:12px;color:var(--text)}

/* video banner */
.video-banner{left:24px;top:414px;width:658px;height:66px;border:1px solid var(--grey-line);background:linear-gradient(90deg,#e6e6e6 0%,#cfcfcf 40%,#3a3f4a 50%,#9aa6b5 70%,#e9e9e9 100%);display:flex;align-items:center;justify-content:center}
.video-play{width:40px;height:40px}

/* feedback */
.feedback{left:0;top:502px;width:705px;height:231px;background:var(--grey-bg)}
.section-title{font-family:"Comfortaa",sans-serif;font-weight:700;font-size:17px;color:var(--black)}
.feedback .section-title{position:absolute;left:0;top:24px;width:705px;text-align:center}
.quote{position:absolute;top:60px;width:205px}
.quote p{font-style:italic;font-size:8px;line-height:15.2px;color:var(--text)}
.quote cite{display:block;margin-top:6px;font-style:normal;font-size:8px;font-weight:600;color:var(--orange)}
.feedback-button{position:absolute;left:249px;top:173px;width:208px;height:29px;border:1px solid var(--grey-line);background:var(--off-white);font-family:"Comfortaa",sans-serif;font-size:8.5px;color:var(--black);text-align:center;line-height:27px}

/* promo */
.promo-banner{left:24px;top:757px;width:658px;height:65px;border:1px solid var(--grey-line);background:linear-gradient(90deg,#0f2340,#1c3a63 55%,#2a4f7a);overflow:hidden}
.promo-banner .kicker{position:absolute;left:198px;top:7px;font-size:15px;color:var(--white)}
.promo-banner .headline{position:absolute;left:92px;top:29px;font-size:23px;font-weight:600;color:var(--white)}
.promo-art{position:absolute;left:410px;top:0;width:248px;height:65px;background:linear-gradient(90deg,#2a4f7a,#8fa3ba 40%,#c7ccd3 60%,#3a5e8a)}

/* charities */
.charities .section-title{position:absolute;left:24px;top:845px}
.charity{position:absolute;width:100px;border:1px solid var(--grey-line);background:var(--white);display:flex;align-items:center;justify-content:center;text-align:center;gap:5px;font-size:11px;font-weight:600;color:var(--black)}
.charity i{display:block;width:10px;height:10px;background:var(--black)}

/* side ads */
.ad{position:absolute;left:362px;width:320px;height:105px;border:1px solid var(--grey-line);overflow:hidden}
.ad-system{top:850px;background:linear-gradient(90deg,#f4f4f4 0%,#e9e9e9 50%,#cfd6dd 100%)}
.ad-system .title{position:absolute;left:4px;top:16px;font-size:19px;line-height:28px;font-weight:600;color:var(--black)}
.ad-system .sub{position:absolute;left:32px;top:72px;font-size:11px;font-weight:600;color:#1f4f9a}
.ad-system .maker{position:absolute;left:4px;top:90px;font-size:9px;font-weight:600;color:var(--black)}
.ad-art{position:absolute;right:0;top:0;width:150px;height:105px;background:linear-gradient(135deg,#c9d2db,#7b8794 60%,#3d444c)}
.ad-gadgets{top:967px;background:linear-gradient(90deg,#ececec,#f7f7f7)}
.ad-gadgets .title{position:absolute;left:0;top:5px;width:320px;text-align:center;font-size:10px;letter-spacing:1.5px;color:var(--black)}
.ad-gadgets .art{position:absolute;left:0;top:22px;width:320px;height:83px;background:linear-gradient(90deg,#e7c9b8 0%,#f1f1f1 30%,#9aa3ad 55%,#6c7682 80%,#d9dde2 100%)}

/* footer */
.site-footer{left:0;top:1101px;width:705px;height:99px;background:var(--black);color:var(--white)}
.footer-links{position:absolute;left:24px;top:27px;font-size:8px}
.footer-links span{color:#999;margin:0 6px}
.legal{position:absolute;left:24px;top:49px;font-size:7.5px;line-height:14px;color:#cccccc}
.social{position:absolute;right:20px;top:44px;display:flex;gap:9px;font-size:8px;font-weight:600;color:var(--white)}
</style>
</head>
<body>

<nav class="abs utility-bar">
  <a style="left:24px">notification</a>
  <a style="left:94px">news</a>
  <a style="left:145px">list items</a>
  <a style="left:371px">contact us</a>
  <a style="left:433px">help</a>
  <a style="left:467px">terms</a>
  <a style="left:510px">conditions</a>
  <div class="site-search">
    <span>Search....</span>
    <svg width="10" height="10" viewBox="0 0 10 10"><circle cx="4" cy="4" r="3" fill="none" stroke="#000" stroke-width="1.5"/><line x1="6.3" y1="6.3" x2="9.3" y2="9.3" stroke="#000" stroke-width="1.6"/></svg>
  </div>
</nav>

<header class="abs masthead">
  <div class="brand">VELMA</div>
  <nav class="main-nav">
    <a style="left:315px">shopping basket</a>
    <a style="left:410px">wishlist</a>
    <a style="left:464px">sign in</a>
    <a style="left:515px">my account</a>
    <a style="left:591px">my recent searches</a>
  </nav>
</header>

<section class="abs hero">
  <div class="media-tile" style="left:24px;top:26px;width:206px;height:120px;background:linear-gradient(135deg,#5b6470,#2e343c 60%,#8c8f93)" role="img" aria-label="Video still of a laptop on a desk during a video call">
    <svg class="play-ring" viewBox="0 0 30 30"><circle cx="15" cy="15" r="13" fill="none" stroke="#fff" stroke-width="2.5"/><path d="M12 9 L21 15 L12 21 Z" fill="#fff"/></svg>
  </div>
  <div class="media-tile" style="left:24px;top:158px;width:206px;height:122px;background:linear-gradient(135deg,#6b5446,#4a3a30 60%,#8a7060)" role="img" aria-label="Video still of a smartphone lying on a wooden table">
    <svg class="play-ring" viewBox="0 0 30 30"><circle cx="15" cy="15" r="13" fill="none" stroke="#fff" stroke-width="2.5"/><path d="M12 9 L21 15 L12 21 Z" fill="#fff"/></svg>
  </div>

  <form class="search-panel">
    <h2>search</h2>
    <span class="field-label" style="top:40px">Items</span>
    <div class="field" style="top:56px">Enter Item</div><span class="help-dot" style="top:63px">?</span>
    <span class="field-label" style="top:85px">Location</span>
    <div class="field" style="top:101px">Enter Location</div><span class="help-dot" style="top:108px">?</span>
    <span class="field-label" style="top:128px">From</span>
    <div class="field" style="top:144px">£</div><span class="help-dot" style="top:151px">?</span>
    <span class="field-label" style="top:172px">To</span>
    <div class="field" style="top:187px">£</div><span class="help-dot" style="top:194px">?</span>
    <div class="search-button">search</div>
  </form>

  <article class="item-card" style="top:26px">
    <div class="item-thumb" role="img" aria-label="Photo of a wristwatch" style="background:linear-gradient(135deg,#1e2630,#6b7480 50%,#2b3138)"></div>
    <h3>item title</h3>
    <p>Vestibulum ante ipsum primis in faucibus orci luctus et ultrices posuere cubilia</p>
  </article>
  <article class="item-card" style="top:114px">
    <div class="item-thumb" role="img" aria-label="Photo of a laptop" style="background:linear-gradient(135deg,#f0f0f0,#9a9ea3 50%,#e4e4e4)"></div>
    <h3>item title</h3>
    <p>Vestibulum ante ipsum primis in faucibus orci luctus et ultrices posuere cubilia</p>
  </article>
  <article class="item-card" style="top:202px">
    <div class="item-thumb" role="img" aria-label="Photo of a smartphone" style="background:linear-gradient(135deg,#6b5446,#c9ccd0 50%,#4a3a30)"></div>
    <h3>item title</h3>
    <p>Vestibulum ante ipsum primis in faucibus orci luctus et ultrices posuere cubilia</p>
  </article>
</section>

<div class="abs video-banner" role="img" aria-label="Video banner showing devices and glasses on a wooden desk">
  <svg class="video-play" viewBox="0 0 40 40"><circle cx="20" cy="20" r="18" fill="rgba(0,0,0,0.35)" stroke="#fff" stroke-width="2.5"/><path d="M16 12 L28 20 L16 28 Z" fill="#fff"/></svg>
</div>

<section class="abs feedback">
  <h2 class="section-title">user feedback</h2>
  <blockquote class="quote" style="left:24px">
    <p>“ Aliquam molestie, mi et imperdiet euismod, dui purus auctor tellus, et interdum lacus lectus et ante. Sed accumsan sollicitudin sapien, sit amet adipiscing turpis gravida ac.”</p>
    <cite>-NAME HEADING</cite>
  </blockquote>
  <blockquote class="quote" style="left:250px">
    <p>“ Aliquam molestie, mi et imperdiet euismod, dui purus auctor tellus, et interdum lacus lectus et ante. Sed accumsan sollicitudin sapien, sit amet adipiscing turpis gravida ac.”</p>
    <cite>-NAME HEADING</cite>
  </blockquote>
  <blockquote class="quote" style="left:477px">
    <p>“ Aliquam molestie, mi et imperdiet euismod, dui purus auctor tellus, et interdum lacus lectus et ante. Sed accumsan sollicitudin sapien, sit amet adipiscing turpis gravida ac.”</p>
    <cite>-NAME HEADING</cite>
  </blockquote>
  <div class="feedback-button">leave feedback for chance to win a prize</div>
</section>

<aside class="abs promo-banner">
  <div class="kicker">Armora</div>
  <div class="headline">Nova X7 | X7 edge</div>
  <div class="promo-art" role="img" aria-label="Row of phones in metallic cases"></div>
</aside>

<section class="charities">
  <h2 class="section-title">charities supported</h2>
  <div class="charity" style="left:24px;top:878px;height:61px"><i></i>Rowan Works</div>
  <div class="charity" style="left:134px;top:878px;height:128px">Little Hearts<br>Fund</div>
  <div class="charity" style="left:244px;top:878px;height:61px">Steadfast Life</div>
  <div class="charity" style="left:24px;top:945px;height:61px"><i></i>Quanda</div>
  <div class="charity" style="left:244px;top:945px;height:61px"><i></i>Stanway</div>
  <div class="charity" style="left:24px;top:1011px;height:61px">Westgate Inns</div>
  <div class="charity" style="left:134px;top:1011px;height:61px">CallCircle</div>
  <div class="charity" style="left:244px;top:1011px;height:61px">Adrona</div>
</section>

<aside class="ad ad-system">
  <div class="ad-art" role="img" aria-label="Control panels, screens and phones"></div>
  <div class="title">The Complete<br>System Solution!</div>
  <div class="sub">HMI - PLC - SCADA</div>
  <div class="maker">Vantor</div>
</aside>
<aside class="ad ad-gadgets">
  <div class="title">FOR GADGET LOVERS</div>
  <div class="art" role="img" aria-label="Hand holding a tablet beside cameras, laptops, watches and phones at affordable prices"></div>
</aside>

<footer class="abs site-footer">
  <div class="footer-links">About Velma<span>|</span>Seafty Hub<span>|</span>ResolutionHub<span>|</span>Vendor Hub<span>|</span>Partner Hub<span>|</span>Charity Hub</div>
  <div class="legal">Copyright © 2017. Company Name. All Right Reserved<br>Advertise on Velma &nbsp;|&nbsp; Site Map</div>
  <div class="social"><span>Pals</span><span>Chirp</span><span>Linkup</span><span>Lenso</span><span>Boardly</span><span>Circlo</span><span>Vidra</span></div>
</footer>

</body>
</html>
```